Computer consultant business card

Qelvo Software is a newly started computer consulting company. It's a small one-man company that provides mostly Vornix applications but also websites in collaboration with designers. I'm running this company on the side of full time university studies.

I want the final design to be clean and memorable. Be creative! :)

Some inspiration:
http://www.pixelmarta.com/design/48317
http://www.pixelmarta.com/design/2739164/business-card-design-by-frostlynk
http://www.pixelmarta.com/design/604281/business-card-design-by-koralind-vestrabanu

See attachment for my company logo.
Updates

I would like to thank everyone for submitting! I'll need a couple of days to review and ultimately select a design.

Target Market(s)

Non-technical entrepreneurs and small companies.

Industry/Entity Type

University

Requirements
Must have
• My company logo.
In any way, both colors from my logo.
First- and last name, e-mail and phone number.
Double-sided design.
Nice to have
• Something creative with the symbol in my logo

```html
<!DOCTYPE html>
<html lang="en">
<head>
<meta charset="utf-8">
<title>Qelvo Software – Business Card</title>
<link rel="stylesheet" href="https://fonts.googleapis.com/css2?family=Arimo:wght@400;700&display=swap">
<style>
  :root {
    --stage: #e6e6e6;
    --card-white: #ffffff;
    --brand-blue: #2a7ff5;
    --brand-dark: #333132;
    --faint-mark: #eef0f4;
    --rule-grey: #9aa3b0;
    --text-white: #ffffff;
  }
  * { box-sizing: border-box; margin: 0; padding: 0; }
  html, body {
    width: 1200px; height: 1022px; overflow: hidden;
    background: var(--stage);
    font-family: "Arimo", Arial, sans-serif;
  }
  .canvas { position: relative; width: 1200px; height: 1022px; }
  .card {
    position: absolute; top: 75px; width: 500px; height: 873px;
    overflow: hidden;
  }
  .card--front { left: 73px; background: var(--card-white); border: 1px solid #cfcfcf; }
  .card--back {
    left: 627px;
    background: radial-gradient(circle at 50% 50%, #ffffff 0%, #cfe2fd 18%, #6ea9f8 45%, var(--brand-blue) 75%);
  }
  .brand-lockup {
    position: absolute; top: 50px; left: 0; width: 100%;
    display: flex; align-items: center; justify-content: center; gap: 24px;
  }
  .brand-lockup__dot {
    width: 96px; height: 96px; border-radius: 50%; background: var(--brand-blue);
  }
  .brand-lockup__name {
    font-size: 92px; font-weight: 700; color: var(--brand-dark);
    letter-spacing: -1px; line-height: 1;
  }
  .brand-watermark {
    position: absolute; top: 420px; left: 0; width: 100%;
    text-align: center; font-size: 140px; font-weight: 700;
    color: var(--faint-mark); line-height: 1;
  }
  .card__rule {
    position: absolute; left: 0; right: 0; top: 670px; height: 3px;
    background: var(--rule-grey);
  }
  .contact-band {
    position: absolute; left: 0; right: 0; bottom: 0; height: 196px;
    background: var(--brand-blue); color: var(--text-white);
  }
  .person {
    position: absolute; right: 270px; top: 58px; text-align: right;
  }
  .person__first { font-size: 33px; font-weight: 700; line-height: 1.15; }
  .person__last { font-size: 26px; font-weight: 400; line-height: 1.15; }
  .contact-band__divider {
    position: absolute; left: 237px; top: 30px; width: 2px; height: 110px;
    background: var(--text-white);
  }
  .contact-list {
    position: absolute; left: 256px; top: 20px; list-style: none;
    font-size: 22px; line-height: 1.5;
  }
  .contact-list li { display: flex; align-items: center; gap: 8px; }
  .contact-list .icon { width: 18px; height: 18px; flex: none; }
  .contact-list .address { margin-top: 12px; line-height: 1.3; }
  .back-lockup {
    position: absolute; top: 0; left: 0; width: 100%; height: 100%;
    display: flex; align-items: center; justify-content: center;
  }
  .back-lockup__name {
    font-size: 130px; font-weight: 700; color: var(--brand-dark); line-height: 1;
  }
</style>
</head>
<body>
<main class="canvas">
  <section class="card card--front" aria-label="Business card front">
    <div class="brand-lockup">
      <span class="brand-lockup__dot" aria-hidden="true"></span>
      <span class="brand-lockup__name">qelvo</span>
    </div>
    <div class="brand-watermark" aria-hidden="true">qelvo</div>
    <div class="card__rule"></div>
    <div class="contact-band">
      <div class="person">
        <p class="person__first">First Name</p>
        <p class="person__last">Last Name</p>
      </div>
      <div class="contact-band__divider"></div>
      <ul class="contact-list">
        <li>
          <svg class="icon" viewBox="0 0 24 24" aria-hidden="true"><path fill="#fff" d="M6.6 10.8a15 15 0 0 0 6.6 6.6l2.2-2.2c.3-.3.7-.4 1-.2 1.1.4 2.3.6 3.6.6.6 0 1 .4 1 1V20c0 .6-.4 1-1 1A17 17 0 0 1 3 4c0-.6.4-1 1-1h3.5c.6 0 1 .4 1 1 0 1.3.2 2.5.6 3.6.1.3 0 .7-.2 1z"/></svg>
          <span>0987 654321</span>
        </li>
        <li>
          <svg class="icon" viewBox="0 0 24 24" aria-hidden="true"><rect x="2" y="5" width="20" height="14" rx="2" fill="#fff"/><path d="M3 6l9 7 9-7" fill="none" stroke="#2a7ff5" stroke-width="2"/></svg>
          <span>info@qelvo.com</span>
        </li>
        <li class="address"><span>00, Complex name<br>City, State 0042</span></li>
      </ul>
    </div>
  </section>

  <section class="card card--back" aria-label="Business card back">
    <div class="back-lockup">
      <span class="back-lockup__name">qelvo</span>
    </div>
  </section>
</main>
</body>
</html>
```